Dovin Sound 862 the new wave for sound to enlighten open ears

This is a music recording studio, we need pictures of a booth, random pictures of anything that will draw interest to a recording studio, we just need the website to reflect a music studio recording website. Apply generic information on the site that correlates with most music studio websites up to date. We want the modern style look that will entice eyes across the nation. Information should be easily accessible on the website. Dovin Sound 862 is owned by Marcellus Okafor located 5176 Bellweather Ln, Miramar, Fl, 33027. Email: Mokaforsound@dovinmail.net and best contact number to date is 417-293-7041. The sound coming out of this location will be radio ready at all times, artist come in one way and come out with more wisdom than before. Its the new way to make music the appropriate way and bring the best out of those willing to reach their peak.

Target Market(s)

Recording Artist

Industry/Entity Type

Recording Studio

Coding

Coded - Design and coding required

Number of Pages Required

1 page

Font styles to use
Sans Serif

Requirements
Must have
• Anything that gives the site a music feel
Nice to have
• microphones, booths, studio mixing desk

```html
<!DOCTYPE html>
<html lang="en">
<head>
<meta charset="utf-8">
<title>Dovin Sound 862 — Music Recording Studio</title>
<link rel="stylesheet" href="https://fonts.googleapis.com/css2?family=Open+Sans:wght@400;600;700;800&family=Oswald:wght@500&display=swap">
<style>
:root{
  --yellow:#f9b400;
  --brown:#6d3b22;
  --brown-dark:#5a2e19;
  --brown-card:#6a3520;
  --ink:#3a3a3a;
  --body:#555;
  --white:#fff;
  --panel:#f4f4f4;
  --footer:#4b4b4b;
  --footer-text:#a9a9a9;
}
*{box-sizing:border-box;margin:0;padding:0}
html,body{width:1200px;height:2679px;overflow:hidden}
body{font-family:"Open Sans",Arial,sans-serif;color:var(--body);background:var(--white);position:relative}
.btn{position:absolute;display:flex;align-items:center;justify-content:center;background:var(--yellow);color:var(--white);font-weight:700;font-size:15px;letter-spacing:.5px;text-transform:uppercase;width:180px;height:48px}
.rule{position:absolute;height:6px;width:90px;background:var(--yellow)}

/* hero */
.hero{position:absolute;left:0;top:0;width:1200px;height:664px;overflow:hidden}
.hero-photo{position:absolute;inset:0;background:radial-gradient(ellipse at 55% 45%,#8a5a34 0%,#5a361d 40%,#2a1a10 80%,#180e08 100%)}
.nav a{position:absolute;top:54px;color:var(--white);font-size:12.5px;font-weight:700;text-decoration:none;letter-spacing:.3px}
.brand{position:absolute;top:30px;left:0;width:1200px;text-align:center;color:var(--white);font-family:"Oswald","Arial Narrow",sans-serif;font-size:42px;font-weight:500;line-height:64px;letter-spacing:0}
.hero-title{position:absolute;left:75px;top:292px;color:var(--yellow);font-size:50px;font-weight:800;letter-spacing:.5px}
.hero-sub{position:absolute;left:75px;top:357px;color:var(--white);font-size:30px;font-weight:800}
.dots{position:absolute;left:75px;top:616px;display:flex;gap:7px}
.dots span{width:14px;height:14px;border-radius:50%;background:var(--white)}
.dots span:first-child{background:var(--yellow)}
.quick{position:absolute;left:859px;top:471px;width:341px;height:193px;background:rgba(0,0,0,.85);border-left:6px solid var(--yellow);padding:18px 0 0 17px;color:var(--white)}
.quick h3{font-size:24px;font-weight:700;margin-bottom:14px}
.quick p{font-size:15px;font-weight:600;line-height:22px}
.quick .row{display:flex;align-items:center;gap:14px;margin-top:7px;font-size:15px;font-weight:600}
.quick svg{width:16px;height:16px;flex:none}

/* welcome */
.welcome{position:absolute;left:0;top:664px;width:1200px;height:384px}
.sec-title{position:absolute;left:0;width:1200px;text-align:center;color:var(--ink);font-size:34px;font-weight:800}
.welcome p{position:absolute;left:70px;top:136px;width:1060px;text-align:center;font-size:15px;line-height:29px}

/* feature bands */
.band{position:absolute;left:0;width:1200px;height:398px;background:linear-gradient(90deg,#6a381f,#7a4427 50%,#6a381f);overflow:hidden}
.band-photo{position:absolute;top:0;height:398px}
.band h2{position:absolute;color:var(--white);font-size:32px;font-weight:800}
.band .ruleb{position:absolute;height:6px;width:90px;background:var(--yellow)}
.band p{position:absolute;color:var(--white);font-size:15px;line-height:28.5px;width:505px}
.about{top:1048px}
.about .band-photo{left:0;width:590px;clip-path:polygon(0 0,523px 0,589px 100%,0 100%);background:linear-gradient(120deg,#3a2a26,#5c4540 45%,#2a1f1e)}
.service{top:1447px}
.service .band-photo{right:0;width:612px;clip-path:polygon(0 0,100% 0,100% 100%,63px 100%);background:linear-gradient(160deg,#4e4650,#3a2f33 50%,#5a2630)}

/* sessions */
.sessions{position:absolute;left:0;top:1845px;width:1200px;height:673px}
.sessions .lead{position:absolute;top:128px;left:0;width:1200px;text-align:center;font-size:15px}
.card{position:absolute;top:191px;width:330px;height:430px;background:var(--panel)}
.card-head{height:57px;background:var(--brown-card);color:var(--yellow);display:flex;align-items:center;justify-content:center;gap:10px;font-size:17px;font-weight:700;text-transform:uppercase}
.card-head svg{width:17px;height:17px}
.card ul{list-style:none;text-align:center;padding-top:10px}
.card li{height:84px}
.card b{display:block;color:var(--brown-dark);font-size:22px;font-weight:700;line-height:31px}
.card span{display:block;font-size:15px;line-height:21px;padding:0 40px}

/* footer */
.footer{position:absolute;left:0;top:2518px;width:1200px;height:161px;background:var(--footer)}
.footer nav a{position:absolute;top:40px;color:var(--white);font-size:12.5px;font-weight:700;text-decoration:none}
.footer .copy{position:absolute;left:75px;top:78px;color:var(--footer-text);font-size:13px;font-weight:600;line-height:27px}
.social{position:absolute;left:961px;top:47px;display:flex;gap:14px}
.social span{width:22px;height:22px;border-radius:4px;background:var(--white)}
</style>
</head>
<body>

<header class="hero">
  <div class="hero-photo" role="img" aria-label="Recording studio control room with large mixing desk and studio monitors"></div>
  <nav class="nav">
    <a href="#" style="left:75px">HOME</a>
    <a href="#" style="left:175px">ABOUT STUDIO</a>
    <a href="#" style="left:334px">SERVICES</a>
    <a href="#" style="left:797px">SESSIONS</a>
    <a href="#" style="left:918px">PROJECTS</a>
    <a href="#" style="left:1041px">CONTACT US</a>
  </nav>
  <div class="brand">DOVIN SOUND 862</div>
  <h1 class="hero-title">DOVIN SOUND 862</h1>
  <div class="hero-sub">WE ARE A MUSIC RECORDING STUDIO</div>
  <div class="dots"><span></span><span></span><span></span><span></span></div>
  <aside class="quick">
    <h3>QUICK CONTACT</h3>
    <p>5176 Bellweather Ln, Miramar<br>Fl, 33027</p>
    <div class="row"><svg viewBox="0 0 16 16"><rect x="1" y="3" width="14" height="10" rx="1" fill="#fff"/><path d="M1 4l7 5 7-5" stroke="#000" stroke-width="1.4" fill="none"/></svg>Mokaforsound@dovinmail.net</div>
    <div class="row"><svg viewBox="0 0 16 16"><path d="M4 1l3 3-2 2c1 2 3 4 5 5l2-2 3 3-2 2C8 14 2 8 2 3z" fill="#fff"/></svg>417-293-7041</div>
  </aside>
</header>

<section class="welcome">
  <h2 class="sec-title" style="top:46px">WELCOME TO OUR WEBSITE</h2>
  <div class="rule" style="left:555px;top:104px"></div>
  <p>Aliquam molestie, mi et imperdiet euismod, dui purus auctor tellus, et interdum lacus lectus et ante. Sed accumsan sollicitudin sapien, sit amet adipiscing turpis gravida ac. In congue, neque ac lobortis volutpat, libero mauris varius mi, vitae suscipit ipsum ligula vitae risus.<br>Duis aliquam nibh a dui iaculis viverra id a velit. Vivamus egestas risus in magna varius commodo. Sed semper viverra egestas.<br>Etiam pretium porttitor lectus, vel ornare neque porta volutpat.</p>
  <a class="btn" style="left:511px;top:282px">READ MORE</a>
</section>

<section class="band about">
  <div class="band-photo" role="img" aria-label="Sound engineer working at a mixing console in front of monitors"></div>
  <h2 style="left:611px;top:56px">ABOUT DOVIN SOUND 862</h2>
  <div class="ruleb" style="left:611px;top:112px"></div>
  <p style="left:611px;top:140px">Aliquam molestie, mi et imperdiet euismod, dui purus auctor tellus, et interdum lacus lectus et ante. Sed accumsan sollicitudin sapien, sit amet adipiscing turpis gravida ac. In congue, neque ac lobortis volutpat, libero mauris varius mi, vitae suscipit ipsum ligula vitae risus.</p>
  <a class="btn" style="left:611px;top:286px">READ MORE</a>
</section>

<section class="band service">
  <div class="band-photo" role="img" aria-label="Studio desk with audio interfaces, monitors and headphones"></div>
  <h2 style="left:75px;top:52px">OUR SERVICE</h2>
  <div class="ruleb" style="left:75px;top:108px"></div>
  <p style="left:75px;top:139px">Aliquam molestie, mi et imperdiet euismod, dui purus auctor tellus, et interdum lacus lectus et ante. Sed accumsan sollicitudin sapien, sit amet adipiscing turpis gravida ac. In congue, neque ac lobortis volutpat, libero mauris varius mi, vitae suscipit ipsum ligula vitae risus.</p>
  <a class="btn" style="left:75px;top:284px">READ MORE</a>
</section>

<section class="sessions">
  <h2 class="sec-title" style="top:40px">OUR SESSIONS</h2>
  <div class="rule" style="left:555px;top:96px"></div>
  <p class="lead">Aliquam molestie, mi et imperdiet euismod, dui purus auctor tellus, et interdum lacus lectus et ante.</p>

  <article class="card" style="left:75px">
    <div class="card-head"><svg viewBox="0 0 16 16"><path d="M6 2l9-2v11a2.5 2 0 1 1-2-2V3L8 4v9a2.5 2 0 1 1-2-2z" fill="currentColor"/></svg>Recording Price</div>
    <ul>
      <li><b>$80</b><span>per hour minimum 4 hours required</span></li>
      <li><b>$75</b><span>per hour minimum 8 hours required</span></li>
      <li><b>$70</b><span>per hour minimum 12 hours required</span></li>
      <li><b>$90</b><span>for individual hours, packages recommended</span></li>
    </ul>
  </article>

  <article class="card" style="left:434px">
    <div class="card-head"><svg viewBox="0 0 18 16"><circle cx="9" cy="4" r="3" fill="currentColor"/><circle cx="3.5" cy="5" r="2" fill="currentColor"/><circle cx="14.5" cy="5" r="2" fill="currentColor"/><path d="M4 14c0-4 2-6 5-6s5 2 5 6z" fill="currentColor"/><path d="M0 13c0-3 1-5 3.5-5 1 0 1.5.3 2 .7C4 10 3.5 11 3.3 13zM18 13c0-3-1-5-3.5-5-1 0-1.5.3-2 .7 1.5 1.3 2 2.3 2.2 4.3z" fill="currentColor"/></svg>Memberships Deals</div>
    <ul>
      <li><b>$1500</b><span>get 48 recording hours in addition to 24 hours mix down</span></li>
      <li><b>$2500</b><span>get 48 recording hours in addition to 24 hours mix down</span></li>
      <li><b>$3500</b><span>get 48 recording hours in addition to 24 hours mix down</span></li>
    </ul>
  </article>

  <article class="card" style="left:795px">
    <div class="card-head"><svg viewBox="0 0 10 16"><text x="5" y="14" text-anchor="middle" font-family="Open Sans,sans-serif" font-weight="700" font-size="16" fill="currentColor">$</text></svg>Mix Down Only Prices</div>
    <ul>
      <li><b>$50</b><span>per hour minimum 4 hours required</span></li>
      <li><b>$45</b><span>per hour minimum 8 hours required</span></li>
      <li><b>$40</b><span>per hour minimum 12 hours required</span></li>
      <li><b>$60</b><span>for individual hours, packages recommended</span></li>
    </ul>
  </article>
</section>

<footer class="footer">
  <nav>
    <a href="#" style="left:75px">HOME</a>
    <a href="#" style="left:156px">ABOUT STUDIO</a>
    <a href="#" style="left:297px">SERVICES</a>
    <a href="#" style="left:399px">SESSIONS</a>
    <a href="#" style="left:502px">PROJECTS</a>
    <a href="#" style="left:607px">CONTACT US</a>
  </nav>
  <div class="copy">Copyright © 2017 Company Name.<br>All Right Reserved</div>
  <div class="social" aria-label="Social links"><span></span><span></span><span></span><span></span><span></span></div>
</footer>

</body>
</html>
```